New Bicycle shop business card

Hi!
I'm looking for a business card for my new proffesional bike mechanics shop. This shop is only for fixing broken bikes and not selling bikes.
Peferbly a modern and sleek and modern design.
Colors: black, grey, red, white
Information:
Name: Rijwielwerkplaats Vanhoutte
Shop owner: Bart Vanhoutte & Marieke Segers
Website: www.rijwielwerkplaats-vanhoutte.be
Email: info@rijwielwerkplaats-vanhoutte.be
Phone number: +32471902368
Street adres: Kerkweg 46
9940 Bellebeke
Slogan/shop information: Herstellingen van alle merken.
Logo: see files.
Target Market(s)
People who seek a mechanic to fix or upgrade their bikes.
Contact Information for Business Card
Information:
Website: info@rijwielwerkplaats-vanhoutte.be
9940 Bellebeke
Logo: see files.

```html
<!DOCTYPE html>
<html lang="nl">
<head>
<meta charset="utf-8">
<title>Rijwielwerkplaats Vanhoutte – Business Card</title>
<link rel="stylesheet" href="https://fonts.googleapis.com/css2?family=Roboto:wght@400;500;700&family=Josefin+Sans:wght@700&display=swap">
<style>
  :root {
    --backdrop: #3b3734;
    --ink-dark: #1d1414;
    --ink-text: #2a2a2a;
    --brand-red: #e02b3c;
    --brand-grey: #a5a5a5;
    --paper: #ffffff;
  }
  * { box-sizing: border-box; margin: 0; padding: 0; }
  html, body { width: 1200px; height: 909px; overflow: hidden; }
  body {
    background: var(--backdrop);
    font-family: "Roboto", Arial, sans-serif;
    position: relative;
  }
  .card {
    position: absolute;
    top: 273px;
    width: 560px;
    height: 362px;
    border-radius: 3px;
    overflow: hidden;
    box-shadow: 0 10px 30px rgba(0,0,0,.45);
  }
  /* Back side */
  .card-back { left: 20px; background: var(--ink-dark); }
  .back-mark {
    position: absolute; inset: 0;
    display: flex; flex-direction: column; align-items: center; justify-content: center; gap: 16px;
  }
  .mark-dot { width: 64px; height: 64px; border-radius: 50%; background: var(--brand-red); }
  .back-name {
    font-family: "Josefin Sans", "Roboto", sans-serif;
    font-weight: 700; font-size: 22px; letter-spacing: 2px;
    color: var(--paper); text-transform: uppercase; text-align: center; line-height: 1.25;
  }
  /* Front side */
  .card-front { left: 620px; background: var(--paper); }
  .front-mark {
    position: absolute; left: 22px; top: 92px; width: 228px;
    display: flex; flex-direction: column; align-items: center; gap: 14px;
  }
  .front-mark .mark-dot { width: 54px; height: 54px; }
  .front-name {
    font-family: "Josefin Sans", "Roboto", sans-serif;
    font-weight: 700; font-size: 19px; letter-spacing: 1.5px; line-height: 1.3;
    color: var(--ink-dark); text-transform: uppercase; text-align: center;
  }
  .details { position: absolute; left: 268px; top: 44px; right: 14px; color: var(--ink-text); }
  .shop-title { color: var(--brand-red); font-weight: 500; font-size: 18px; line-height: 1.1; }
  .owners { font-size: 11.5px; margin-top: 4px; }
  .address { font-size: 12.5px; margin-top: 18px; line-height: 1.35; }
  .contact-list { list-style: none; margin-top: 16px; font-size: 12px; }
  .contact-list li { display: flex; align-items: center; gap: 10px; height: 20px; }
  .contact-list svg { width: 12px; height: 12px; flex: none; fill: var(--brand-red); }
  .front-bands { position: absolute; left: 0; bottom: 0; width: 560px; height: 70px; }
  .slogan {
    position: absolute; right: 16px; bottom: 40px;
    color: var(--paper); font-size: 13px; letter-spacing: .3px;
  }
</style>
</head>
<body>

<section class="card card-back" aria-label="Achterkant visitekaartje">
  <div class="back-mark">
    <span class="mark-dot"></span>
    <p class="back-name">Rijwielwerkplaats<br>Vanhoutte</p>
  </div>
</section>

<section class="card card-front" aria-label="Voorkant visitekaartje">
  <div class="front-mark">
    <span class="mark-dot"></span>
    <p class="front-name">Rijwielwerkplaats<br>Vanhoutte</p>
  </div>

  <div class="details">
    <h1 class="shop-title">Rijwielwerkplaats Vanhoutte</h1>
    <p class="owners">Shop owner. Bart Vanhoutte &amp; Marieke Segers</p>
    <p class="address">Kerkweg 46<br>9940 Bellebeke</p>
    <ul class="contact-list">
      <li>
        <svg viewBox="0 0 24 24" aria-hidden="true"><path d="M6.6 10.8a15.1 15.1 0 0 0 6.6 6.6l2.2-2.2a1 1 0 0 1 1-.25 11.4 11.4 0 0 0 3.6.57 1 1 0 0 1 1 1V20a1 1 0 0 1-1 1A17 17 0 0 1 3 4a1 1 0 0 1 1-1h3.5a1 1 0 0 1 1 1c0 1.25.2 2.45.57 3.57a1 1 0 0 1-.25 1z"/></svg>
        +32471902368
      </li>
      <li>
        <svg viewBox="0 0 24 24" aria-hidden="true"><path d="M2 5h20v14H2z M4 7v.5l8 5 8-5V7z" fill-rule="evenodd"/></svg>
        info@rijwielwerkplaats-vanhoutte.be
      </li>
      <li>
        <svg viewBox="0 0 24 24" aria-hidden="true"><path d="M12 2a10 10 0 1 0 0 20 10 10 0 0 0 0-20zm0 3a7 7 0 0 1 6.9 6h-3.2a11 11 0 0 0-1.6-5.7A7 7 0 0 1 12 5zm-2.1.3A11 11 0 0 0 8.3 11H5.1a7 7 0 0 1 4.8-5.7zM5.1 13h3.2a11 11 0 0 0 1.6 5.7A7 7 0 0 1 5.1 13zm9 5.7a11 11 0 0 0 1.6-5.7h3.2a7 7 0 0 1-4.8 5.7z"/></svg>
        www.rijwielwerkplaats-vanhoutte.be
      </li>
    </ul>
  </div>

  <svg class="front-bands" viewBox="0 0 560 70" aria-hidden="true">
    <rect x="0" y="44" width="560" height="26" fill="var(--ink-dark)"/>
    <polygon points="318,44 336,8 560,8 560,44" fill="var(--brand-red)"/>
  </svg>
  <p class="slogan">Herstellingen van alle merken.</p>
</section>

</body>
</html>
```